A4 6 page tri-fold brochure for security screen company

Brochure design and layout for a new company based in the UAE called Harbor Grilles. We make clear mesh security screen doors and windows that aesthetically blend with the house, like a fly screen, rather than a traditional heavy looking security screen. We want to project an image of safety and security but with warmth and humanity to it, not just something clinical. Copy hasn't been written yet so use dummy text or pull and adjust copy form our website www.harborgrilles.ae.
Target market: home owners, financially comfortable, possibly with young children or pets.
Purpose of brochure: to have potential clients contact us (via phone, whatsapp, email or through our website) to arrange a free measure and quote.
More details provided in attached word doc brief and product images, logos etc, attached also.
Please see attached brief.

Target Market(s)

Home owners, financially comfortable, possibly with young children or pets.

Industry/Entity Type

Home Improvement

Font styles to use
Serif
Sans Serif

Colors
0255a3
3176b5
85acd3
cfdfed
eaf1f7

Requirements
Must have
• Good clear images with detailed close ups (or call outs) of specific details such as the mesh and locks.
• Contact details to include website www.harborgrilles.ae, phone number: +971 50 318 2094, email address: oliver@harborgrilles.ae
Nice to have
• If your are comfortable using and adjusting the appropriate copy from our website please do so.
• Images - I've included a lot of images so please choose the most appropriate to help sell the product. Some of the better images I like are: _DSC2929, French_Windows, HARBOR_GRILLES-3204, HARBOR_GRILLES-3231, HARBOR_GRILLES-3345, HARBOR_GRILLES-3354, HARBOR_GRILLES-3401, Girls room windows1, Girls room windows2, IMG_2968. Please don't limit yourself to these images and use the ones you feel best fit.
Should not have
• Please see attached brief.

```html
<!DOCTYPE html>
<html lang="en">
<head>
<meta charset="utf-8">
<title>Harbor Grilles – Tri-fold Brochure</title>
<link rel="stylesheet" href="https://fonts.googleapis.com/css2?family=Michroma&family=Montserrat:ital,wght@0,400;0,600;0,700;1,600&display=swap">
<style>
  :root{
    --blue:#0255a3;
    --blue-mid:#3176b5;
    --blue-soft:#85acd3;
    --blue-pale:#cfdfed;
    --blue-mist:#eaf1f7;
    --navy:#1c3d6e;
    --ink:#4a4f57;
    --paper:#ffffff;
    --stage:#e4e5e7;
    --mesh:#3c4150;
  }
  *{box-sizing:border-box;margin:0;padding:0}
  html,body{width:1200px;height:1200px;overflow:hidden;background:var(--stage)}
  body{position:relative;font-family:"Montserrat",sans-serif;color:var(--ink)}
  .spread{position:absolute;left:202px;display:flex;box-shadow:0 6px 18px rgba(0,0,0,.18)}
  .spread--inside{top:24px}
  .spread--outside{top:614px}
  .panel{position:relative;width:265px;height:562px;background:var(--paper);overflow:hidden}
  .panel + .panel{border-left:1px solid #ececec}
  .panel__art{position:absolute;inset:0;width:265px;height:562px}
  .heading{position:absolute;font-family:"Michroma",sans-serif;color:var(--blue);font-size:8.5px;letter-spacing:.4px;text-transform:uppercase}
  .heading--rule{padding-bottom:3px;border-bottom:1px solid var(--blue-soft)}
  .sub{font-family:"Michroma",sans-serif;color:var(--blue);font-size:7px;text-transform:uppercase;margin-bottom:3px}
  .sub--title{font-size:8px}
  .copy{position:absolute;font-size:5.6px;line-height:1.45}
  .copy p + p{margin-top:3px}
  .banner-title{position:absolute;left:20px;top:34px;color:#fff;font-family:"Michroma",sans-serif;font-weight:400;line-height:1}
  .banner-title .big{font-size:20px;display:block}
  .banner-title .small{font-size:13px;display:block;margin-top:4px}
  .brand{position:absolute;left:40px;top:322px;display:flex;align-items:center;gap:8px}
  .brand__mark{width:18px;height:18px;background:var(--blue)}
  .brand__name{font-family:"Michroma",sans-serif;color:var(--blue);font-size:12px;letter-spacing:1px}
  .tagline{position:absolute;left:0;right:0;top:372px;text-align:center;font-family:"Michroma",sans-serif;color:var(--blue)}
  .tagline__lead{font-size:8.5px;letter-spacing:.3px}
  .tagline__band{margin:8px 0;background:var(--blue);color:#fff;font-family:"Montserrat",sans-serif;font-style:italic;font-weight:600;font-size:12px;padding:5px 0}
  .tagline__tail{font-size:7.5px}
  .tagline__web{margin-top:14px;font-family:"Montserrat",sans-serif;font-weight:600;font-size:8px;letter-spacing:1.5px}
  .contact{position:absolute;left:24px;right:24px;top:330px}
  .contact__title{font-family:"Michroma",sans-serif;color:var(--blue);font-size:11px;text-transform:uppercase;padding-bottom:4px;border-bottom:1px solid var(--blue-soft);display:inline-block}
  .contact__intro{margin-top:10px;font-size:6.5px;line-height:1.5}
  .contact__list{list-style:none;margin-top:16px}
  .contact__item{display:flex;align-items:center;gap:10px;margin-bottom:12px;font-size:8.5px;font-weight:600;color:var(--blue)}
  .contact__icon{width:22px;height:22px;flex:none}
</style>
</head>
<body>

<!-- Inside spread -->
<section class="spread spread--inside">

  <article class="panel panel--info">
    <svg class="panel__art" viewBox="0 0 265 562">
      <defs>
        <linearGradient id="villa" x1="0" y1="0" x2="0" y2="1">
          <stop offset="0" stop-color="#efe6d2"/><stop offset=".6" stop-color="#ddd3bf"/><stop offset="1" stop-color="#8d8a86"/>
        </linearGradient>
        <linearGradient id="room" x1="0" y1="0" x2="1" y2="1">
          <stop offset="0" stop-color="#e9e2d6"/><stop offset="1" stop-color="#8c8275"/>
        </linearGradient>
      </defs>
      <polygon points="0,345 265,300 265,562 0,562" fill="url(#villa)" role="img" aria-label="Photo of villa patio with sliding mesh screen doors"/>
      <polygon points="38,270 112,270 150,322 112,374 38,374 0,322" fill="var(--mesh)" role="img" aria-label="Close-up of woven security mesh"/>
      <polygon points="100,320 142,320 162,350 142,380 100,380 80,350" fill="none" stroke="#fff" stroke-width="3"/>
    </svg>
    <h2 class="heading heading--rule" style="left:18px;top:22px">General Info</h2>
    <div class="copy" style="left:18px;top:42px;width:230px">
      <p>Lorem Ipsum is simply dummy text of the printing and typesetting industry. Lorem Ipsum has been the industry's standard dummy text ever since the 1500s, when an unknown printer took a galley of type and scrambled it to make a type specimen book.</p>
      <p>It has survived not only five centuries, but also the leap into electronic typesetting, remaining essentially unchanged.</p>
    </div>
    <h2 class="heading" style="left:18px;top:118px">Primary Benefits</h2>
    <div class="copy" style="left:18px;top:134px;width:230px">
      <p>Lorem Ipsum is simply dummy text of the printing and typesetting industry. Lorem Ipsum has been the industry's standard dummy text ever since the 1500s, when an unknown printer took a galley of type.</p>
      <p>Lorem Ipsum is simply dummy text of the printing and typesetting industry. It has survived not only five centuries, but also the leap into electronic typesetting, remaining essentially unchanged.</p>
      <p>Lorem Ipsum is simply dummy text of the printing and typesetting industry, remaining essentially unchanged.</p>
    </div>
  </article>

  <article class="panel panel--sliding">
    <svg class="panel__art" viewBox="0 0 265 562">
      <polygon points="0,300 150,250 265,330 265,562 0,562" fill="url(#villa)" role="img" aria-label="Photo of villa terrace with sliding screen doors"/>
      <polygon points="195,470 265,435 265,562 205,562" fill="var(--blue)"/>
      <polygon points="38,55 92,55 120,102 92,150 38,150 10,102" fill="url(#room)" role="img" aria-label="Photo of sliding screen door opening to a balcony"/>
      <polygon points="14,128 32,128 41,141 32,154 14,154 5,141" fill="none" stroke="var(--blue-mid)" stroke-width="1.8"/>
      <polygon points="170,145 230,145 258,188 230,232 170,232 142,188" fill="#d9c7a8" role="img" aria-label="Photo of sliding screen doors in a sand-coloured wall"/>
      <polygon points="150,210 166,210 174,221 166,232 150,232 142,221" fill="none" stroke="var(--blue-mid)" stroke-width="1.8"/>
    </svg>
    <h2 class="heading heading--rule" style="left:22px;top:22px">Sliding Screen Doors</h2>
    <div class="copy" style="left:128px;top:66px;width:125px">
      <h3 class="sub">Lorem Ipsum</h3>
      <p>Lorem Ipsum is simply dummy text of the printing and typesetting industry. Lorem Ipsum has been the industry's standard dummy text ever since the 1500s.</p>
      <p>It has survived not only five centuries, but also the leap into electronic typesetting.</p>
    </div>
    <div class="copy" style="left:14px;top:160px;width:122px">
      <h3 class="sub" style="text-align:right">Lorem Ipsum</h3>
      <p>Lorem Ipsum is simply dummy text of the printing and typesetting industry. Lorem Ipsum has been the industry's standard dummy text ever since the 1500s.</p>
      <p>It has survived not only five centuries, but also the leap into electronic typesetting.</p>
    </div>
  </article>

  <article class="panel panel--range">
    <svg class="panel__art" viewBox="0 0 265 562">
      <polygon points="40,30 94,30 122,78 94,126 40,126 12,78" fill="#6b4a36" role="img" aria-label="Photo of hinged wooden door with mesh screen"/>
      <polygon points="18,104 36,104 45,117 36,130 18,130 9,117" fill="none" stroke="var(--blue-mid)" stroke-width="1.8"/>
      <polygon points="66,180 120,180 148,228 120,276 66,276 38,228" fill="#d8dcd6" role="img" aria-label="Photo of French doors fitted with screens"/>
      <polygon points="44,254 62,254 71,267 62,280 44,280 35,267" fill="none" stroke="var(--blue-mid)" stroke-width="1.8"/>
      <polygon points="40,370 94,370 122,418 94,466 40,466 12,418" fill="#b9cfd9" role="img" aria-label="Photo of French windows with mesh screens"/>
      <polygon points="18,444 36,444 45,457 36,470 18,470 9,457" fill="none" stroke="var(--blue-mid)" stroke-width="1.8"/>
    </svg>
    <div class="copy" style="left:135px;top:42px;width:118px">
      <h2 class="sub sub--title">Hinged Doors</h2>
      <h3 class="sub">Lorem Ipsum</h3>
      <p>Lorem Ipsum is simply dummy text of the printing and typesetting industry. Lorem Ipsum has been the industry's standard dummy text ever since the 1500s.</p>
    </div>
    <div class="copy" style="left:156px;top:192px;width:100px">
      <h2 class="sub sub--title">French Doors</h2>
      <h3 class="sub">Lorem Ipsum</h3>
      <p>Lorem Ipsum is simply dummy text of the printing and typesetting industry. Lorem Ipsum has been the industry's standard dummy text ever since the 1500s.</p>
    </div>
    <div class="copy" style="left:135px;top:382px;width:118px">
      <h2 class="sub sub--title">French Windows</h2>
      <h3 class="sub">Lorem Ipsum</h3>
      <p>Lorem Ipsum is simply dummy text of the printing and typesetting industry. Lorem Ipsum has been the industry's standard dummy text ever since the 1500s.</p>
    </div>
  </article>
</section>

<!-- Outside spread: product details, back, cover -->
<section class="spread spread--outside">

  <article class="panel panel--details">
    <svg class="panel__art" viewBox="0 0 265 562">
      <polygon points="0,18 265,30 265,82 128,138 0,98" fill="var(--blue)"/>
      <polygon points="185,62 225,62 245,96 225,130 185,130 165,96" fill="none" stroke="var(--navy)" stroke-width="3"/>
      <polygon points="38,150 92,150 120,198 92,246 38,246 10,198" fill="#c9bfae" role="img" aria-label="Photo of window with mesh security screen"/>
      <polygon points="16,226 34,226 43,239 34,252 16,252 7,239" fill="none" stroke="var(--blue-mid)" stroke-width="1.8"/>
      <polygon points="84,258 136,258 163,304 136,350 84,350 57,304" fill="#a7a496" role="img" aria-label="Photo of sliding screen door beside a potted palm"/>
      <polygon points="62,330 80,330 89,343 80,356 62,356 53,343" fill="none" stroke="var(--blue-mid)" stroke-width="1.8"/>
      <polygon points="38,368 92,368 120,416 92,464 38,464 10,416" fill="#dcd8d0" role="img" aria-label="Photo of interior window with screen"/>
      <polygon points="16,444 34,444 43,457 34,470 16,470 7,457" fill="none" stroke="var(--blue-mid)" stroke-width="1.8"/>
    </svg>
    <h2 class="banner-title"><span class="big">PRODUCT</span><span class="small">DETAILS</span></h2>
    <div class="copy" style="left:132px;top:166px;width:122px">
      <h3 class="sub">Lorem Ipsum</h3>
      <p>Lorem Ipsum is simply dummy text of the printing and typesetting industry. Lorem Ipsum has been the industry's standard dummy text ever since the 1500s.</p>
      <p>It has survived not only five centuries, remaining essentially unchanged.</p>
    </div>
    <div class="copy" style="left:170px;top:272px;width:88px">
      <h3 class="sub">Lorem Ipsum</h3>
      <p>Lorem Ipsum is simply dummy text of the printing and typesetting industry, ever since the 1500s.</p>
    </div>
    <div class="copy" style="left:132px;top:384px;width:122px">
      <h3 class="sub">Lorem Ipsum</h3>
      <p>Lorem Ipsum is simply dummy text of the printing and typesetting industry. Lorem Ipsum has been the industry's standard dummy text ever since the 1500s.</p>
    </div>
  </article>

  <article class="panel panel--back">
    <svg class="panel__art" viewBox="0 0 265 562">
      <polygon points="0,0 265,0 265,250 132,300 0,250" fill="var(--blue-mist)"/>
      <polygon points="90,80 175,80 218,155 175,230 90,230 47,155" fill="#d6cbb6" role="img" aria-label="Photo of family room with screened window"/>
      <polygon points="60,200 88,200 102,224 88,248 60,248 46,224" fill="none" stroke="var(--blue-mid)" stroke-width="2"/>
      <polygon points="0,520 265,490 265,562 0,562" fill="var(--blue)"/>
    </svg>
    <div class="contact">
      <h2 class="contact__title">Contact Us</h2>
      <p class="contact__intro">Call, message or email us to arrange a free measure and quote.</p>
      <ul class="contact__list">
        <li class="contact__item">
          <svg class="contact__icon" viewBox="0 0 22 22"><circle cx="11" cy="11" r="11" fill="var(--blue)"/><path d="M7.5 6h2l1 2.5-1.3 1a6 6 0 0 0 3.3 3.3l1-1.3 2.5 1v2a1.2 1.2 0 0 1-1.3 1.2A9 9 0 0 1 6.3 7.3 1.2 1.2 0 0 1 7.5 6z" fill="#fff"/></svg>
          <span>+971 50 318 2094</span>
        </li>
        <li class="contact__item">
          <svg class="contact__icon" viewBox="0 0 22 22"><circle cx="11" cy="11" r="11" fill="var(--blue)"/><rect x="5.5" y="7" width="11" height="8" rx="1" fill="#fff"/><path d="M5.8 7.5 11 11.5l5.2-4" fill="none" stroke="var(--blue)" stroke-width="1"/></svg>
          <span>oliver@harborgrilles.ae</span>
        </li>
        <li class="contact__item">
          <svg class="contact__icon" viewBox="0 0 22 22"><circle cx="11" cy="11" r="11" fill="var(--blue)"/><circle cx="11" cy="11" r="5.5" fill="none" stroke="#fff" stroke-width="1"/><ellipse cx="11" cy="11" rx="2.4" ry="5.5" fill="none" stroke="#fff" stroke-width="1"/><line x1="5.5" y1="11" x2="16.5" y2="11" stroke="#fff" stroke-width="1"/></svg>
          <span>www.harborgrilles.ae</span>
        </li>
      </ul>
    </div>
  </article>

  <article class="panel panel--cover">
    <svg class="panel__art" viewBox="0 0 265 562">
      <defs>
        <linearGradient id="facade" x1="0" y1="0" x2="0" y2="1">
          <stop offset="0" stop-color="#cfe0ef"/><stop offset=".35" stop-color="#efe7d4"/><stop offset="1" stop-color="#d9cdb5"/>
        </linearGradient>
      </defs>
      <polygon points="42,40 265,0 265,230 150,292 42,232" fill="url(#facade)" role="img" aria-label="Photo of two-storey villa with screened windows and balcony"/>
      <polygon points="28,62 42,52 42,240 28,252" fill="var(--blue)"/>
      <polygon points="180,205 265,178 265,262 180,290" fill="#8f9196"/>
      <polygon points="50,200 100,200 126,244 100,288 50,288 24,244" fill="var(--mesh)" role="img" aria-label="Close-up of security mesh weave"/>
      <polygon points="46,196 104,196 131,244 104,292 46,292 19,244" fill="none" stroke="var(--navy)" stroke-width="2"/>
    </svg>
    <div class="brand">
      <span class="brand__mark"></span>
      <span class="brand__name">HARBOR GRILLES</span>
    </div>
    <div class="tagline">
      <p class="tagline__lead">SERIOUSLY STRONG SCREENS</p>
      <p class="tagline__band">that let the breeze in and</p>
      <p class="tagline__tail">KEEP INTRUDERS (AND BUGS) OUT!</p>
      <p class="tagline__web">www.harborgrilles.ae</p>
    </div>
  </article>
</section>

</body>
</html>
```